Business Card Design for Brightlane

The company provides engineering tender consulting services and personnel resources. The target market is large engineering construction and services companies. The business is based in Australia.

```html
<!DOCTYPE html>
<html lang="en">
<head>
<meta charset="utf-8">
<title>Brightlane Business Card</title>
<link rel="stylesheet" href="https://fonts.googleapis.com/css2?family=Exo+2:wght@700&family=PT+Sans:wght@400;700&display=swap">
<style>
  :root {
    --stage: #e4e4e2;
    --blue: #2f639f;
    --blue-light: #3f78b6;
    --blue-dark: #285489;
    --stripe: #4aa6e8;
    --ink: #1f2226;
    --grey-ink: #3b3e42;
    --paper: #ffffff;
    --paper-shade: #e4e4e4;
    --brand-font: "Exo 2", sans-serif;
    --body-font: "PT Sans", sans-serif;
  }
  html, body {
    margin: 0;
    width: 1200px;
    height: 973px;
    overflow: hidden;
    background: var(--stage);
  }
  .canvas {
    position: relative;
    width: 1200px;
    height: 973px;
  }
  .card {
    position: absolute;
    top: 117px;
    width: 461px;
    height: 758px;
    border-radius: 10px;
    overflow: hidden;
    box-shadow: 0 6px 18px rgba(0,0,0,0.25);
  }
  .card-front {
    left: 115px;
    background: linear-gradient(180deg, var(--blue-light) 0%, var(--blue) 45%, var(--blue-dark) 100%);
  }
  .card-back {
    left: 600px;
    background: linear-gradient(160deg, var(--paper) 0%, #f3f3f3 55%, var(--paper-shade) 100%);
  }
  .card-shapes {
    position: absolute;
    inset: 0;
  }
  .brand-mark {
    position: absolute;
    background: var(--blue-dark);
    box-shadow: 0 2px 6px rgba(0,0,0,0.25);
  }
  .card-front .brand-mark {
    left: 148px;
    top: 94px;
    width: 116px;
    height: 116px;
  }
  .card-front .brand-name {
    position: absolute;
    left: 0;
    right: 0;
    top: 224px;
    text-align: center;
    font-family: var(--brand-font);
    font-weight: 700;
    font-size: 54px;
    color: var(--paper);
    letter-spacing: 1px;
  }
  .person {
    position: absolute;
    right: 34px;
    top: 528px;
    text-align: right;
    font-family: var(--body-font);
  }
  .person-name {
    font-size: 38px;
    letter-spacing: 1.5px;
    color: var(--grey-ink);
    line-height: 1;
  }
  .person-name .first { color: var(--blue); }
  .person-role {
    margin-top: 6px;
    margin-right: 22px;
    font-size: 19px;
    font-weight: 700;
    letter-spacing: 1.5px;
    color: var(--ink);
  }
  .card-back .brand-mark {
    left: 124px;
    top: 84px;
    width: 62px;
    height: 62px;
    background: #244d80;
  }
  .card-back .brand-name {
    position: absolute;
    left: 22px;
    top: 140px;
    font-family: var(--brand-font);
    font-weight: 700;
    font-size: 38px;
    color: var(--paper);
    letter-spacing: 1px;
  }
  .blurb {
    position: absolute;
    left: 21px;
    top: 290px;
    margin: 0;
    font-family: var(--body-font);
    font-weight: 700;
    font-size: 14.5px;
    letter-spacing: 0.9px;
    line-height: 23.4px;
    color: var(--ink);
    white-space: nowrap;
  }
  .contacts {
    position: absolute;
    left: 28px;
    top: 594px;
    margin: 0;
    padding: 0;
    list-style: none;
    font-family: var(--body-font);
    font-size: 16px;
    letter-spacing: 1px;
    color: var(--ink);
  }
  .contacts li {
    display: flex;
    align-items: center;
    height: 26.5px;
  }
  .contact-icon {
    width: 22px;
    height: 22px;
    margin-right: 17px;
    flex: none;
  }
  .reg-label {
    width: 22px;
    margin-right: 17px;
    font-size: 10px;
    line-height: 10px;
    color: var(--blue);
    text-align: center;
    letter-spacing: 0;
  }
</style>
</head>
<body>
<main class="canvas">

  <section class="card card-front" aria-label="Card front">
    <div class="brand-mark"></div>
    <div class="brand-name">Brightlane</div>
    <svg class="card-shapes" viewBox="0 0 461 758" aria-hidden="true">
      <path d="M85 453 C150 440 200 448 250 458 C330 474 400 470 461 469 L461 656 L85 653 Z" fill="var(--paper)"/>
      <path d="M85 653 L461 656 L461 662 L85 659 Z" fill="rgba(0,0,0,0.12)"/>
      <rect x="0" y="726" width="461" height="3" fill="var(--stripe)"/>
    </svg>
    <div class="person">
      <div class="person-name"><span class="first">Daniel</span> Harper</div>
      <div class="person-role">General Manager</div>
    </div>
  </section>

  <section class="card card-back" aria-label="Card back">
    <svg class="card-shapes" viewBox="0 0 461 758" aria-hidden="true">
      <path d="M0 36 C80 30 170 20 270 12 C275 80 300 160 376 201 C300 214 220 205 150 196 C90 190 40 194 0 202 Z" fill="var(--blue)"/>
      <path d="M270 12 C275 80 300 160 376 201 L368 204 C296 168 268 96 265 14 Z" fill="rgba(0,0,0,0.15)"/>
    </svg>
    <div class="brand-mark"></div>
    <div class="brand-name">Brightlane</div>
    <p class="blurb">your text is hereyour text is hereyour text is here<br>your text is hereyour text is hereyour text is here<br>your text is hereyour text is hereyour text is here<br>your text is hereyour text is hereyour text is here<br>your text is hereyour text is hereyour text is here<br>your text is hereyour text is hereyour text is here<br>your text is hereyour text is hereyour text is here<br>your text is hereyour text is hereyour text is here<br>your text is hereyour text is hereyour text is here<br>your text is hereyour text is hereyour text is here</p>
    <ul class="contacts">
      <li>
        <svg class="contact-icon" viewBox="0 0 22 22" aria-label="Mobile"><rect x="6" y="1" width="10" height="20" rx="2" fill="none" stroke="var(--blue)" stroke-width="2"/><rect x="8" y="4" width="6" height="7" fill="var(--blue)"/></svg>
        999 999 999
      </li>
      <li>
        <svg class="contact-icon" viewBox="0 0 22 22" aria-label="Phone"><path d="M2 9 C2 4 20 4 20 9 L16 10 L15 7 C12 6 10 6 7 7 L6 10 Z" fill="var(--blue)"/><rect x="4" y="11" width="14" height="9" rx="2" fill="var(--blue)"/></svg>
        999 999 999
      </li>
      <li>
        <svg class="contact-icon" viewBox="0 0 22 22" aria-label="Email"><rect x="2" y="5" width="18" height="13" fill="var(--blue)"/><path d="M2 5 L11 12 L20 5" fill="none" stroke="#fff" stroke-width="1.5"/></svg>
        nnnn@nnn.com.au
      </li>
      <li>
        <svg class="contact-icon" viewBox="0 0 22 22" aria-label="Address"><path d="M11 2 L21 11 L18 11 L18 20 L13 20 L13 14 L9 14 L9 20 L4 20 L4 11 L1 11 Z" fill="var(--blue)"/></svg>
        Box 99,Nnnnnnnnn,Nnn,9999
      </li>
      <li>
        <span class="reg-label">Reg<br>No</span>
        ABN99999999999
      </li>
    </ul>
  </section>

</main>
</body>
</html>
```